TA BRAMLEY BUSINESS CARD DESIGN PROJECT

We need to utilize our logo that was expertly created on PixelHarbor and now need to match this with a business card design.

```html
<!DOCTYPE html>
<html lang="en">
<head>
<meta charset="utf-8">
<title>TA BRAMLEY Business Card</title>
<link href="https://fonts.googleapis.com/css2?family=Open+Sans:wght@400;600;700&display=swap" rel="stylesheet">
<style>
  :root {
    --brand-blue: #1456b0;
    --brand-blue-deep: #0f4596;
    --ink-grey: #555a60;
    --card-white: #ffffff;
    --backdrop: #d9d9d7;
  }
  * { box-sizing: border-box; margin: 0; padding: 0; }
  html, body {
    width: 1200px; height: 801px; overflow: hidden;
    background: var(--backdrop);
    font-family: "Open Sans", Arial, sans-serif;
  }
  .stage {
    width: 1200px; height: 801px;
    display: flex; align-items: center; justify-content: center; gap: 40px;
  }
  .card {
    width: 520px; height: 297px; position: relative;
    border-radius: 2px; overflow: hidden;
  }
  .card-front {
    background: var(--card-white);
    border-bottom: 3px solid var(--brand-blue);
  }
  .brand-name {
    color: var(--brand-blue); font-weight: 700; letter-spacing: 0.12em;
  }
  .front-brand {
    position: absolute; top: 44px; right: 70px; font-size: 30px;
  }
  .divider {
    position: absolute; left: 48px; right: 48px; top: 158px;
    height: 1px; background: var(--brand-blue);
  }
  .person {
    position: absolute; left: 48px; top: 104px;
  }
  .person-name {
    color: var(--brand-blue); font-weight: 700; font-size: 19px; letter-spacing: 0.01em;
  }
  .person-title { color: var(--ink-grey); font-size: 14px; margin-top: 1px; }
  .contacts {
    position: absolute; left: 48px; top: 176px; list-style: none;
    color: var(--ink-grey); font-size: 13.5px; line-height: 24px;
  }
  .contacts li { display: flex; align-items: center; gap: 9px; }
  .contacts svg { width: 11px; height: 11px; fill: var(--brand-blue); }
  .address {
    position: absolute; right: 48px; top: 176px; text-align: right;
    color: var(--ink-grey); font-size: 14px; line-height: 22px;
  }
  .card-back {
    background: var(--brand-blue);
  }
  .back-pattern {
    position: absolute; inset: 0;
    background: linear-gradient(120deg, #173f8f 0%, #1456b0 50%, #3c7cc8 100%);
    opacity: 0.9;
  }
  .back-brand {
    position: absolute; left: 50%; top: 50%; transform: translate(-50%, -50%);
    color: var(--card-white); font-size: 28px;
  }
</style>
</head>
<body>
<main class="stage">
  <section class="card card-front" aria-label="Business card front">
    <div class="brand-name front-brand">TA BRAMLEY</div>
    <div class="person">
      <p class="person-name">ROWAN HALE</p>
      <p class="person-title">President</p>
    </div>
    <div class="divider"></div>
    <ul class="contacts">
      <li><svg viewBox="0 0 12 12"><path d="M3 1l2 2.5-1.2 1.3a7 7 0 0 0 3.4 3.4L8.5 7 11 9l-1.3 2A9 9 0 0 1 1 2.3z"/></svg>555-310-4827</li>
      <li><svg viewBox="0 0 12 12"><path d="M0 2h12v1.2L6 7 0 3.2zM0 4.6l6 3.8 6-3.8V10H0z"/></svg>r.hale@tabramley.com</li>
      <li><svg viewBox="0 0 12 12"><circle cx="6" cy="6" r="5.5"/></svg>www.tabramley.com</li>
    </ul>
    <address class="address">1850 Cove Ridge Road<br>Seacliff CA 95003</address>
  </section>
  <section class="card card-back" aria-label="Business card back">
    <div class="back-pattern" role="img" aria-label="Repeating brand pattern in shades of blue"></div>
    <div class="brand-name back-brand">TA BRAMLEY</div>
  </section>
</main>
</body>
</html>
```